Wordpress website design for a Herbal Health Care Company

** Outcome of this project is only the design. Only PSD files of the design for unique pages are sufficient.
** There are a number of unique pages in the new site as shown in the wire-frame. However, for the selection of the designer, Homepage, one 2nd tier page (product category) and one 3rd tier page (product page) is sufficient.
We need web design for our for Ayurvedic & Herbal Products Company located in Sri Lanka
Please get the idea about our company by reading the following text
Vision : To be a world class manufacturer and a supplier of highest quality Ayurvedic pharmaceuticals, Herbal health care products, Herbal cosmetics, Essential oils and Oleoresins
Mission : To provide safe and effective Ayurvedic pharmaceuticals, Herbal health care products and Herbal cosmetics, that is of highest quality and integrity, through the incorporation of ancient ayurvedic wisdom with modern technology and scientific management systems for the inprovement of health and longevity of the people.
Policy on Quality : To design, develop, produce and deliver safe, efficacious and consistent quality Herbal health care products based on Ancient Ayurvedic Wisdom using environmentally preferred process technologies and competent personnel towards continual commitment to total customer satisfaction.
(1) Color theme of the website
You can use the color derived from the company logo
(2) Site Map and description of the site
(1) Home
see the wire frame
http://clipmora.net/t/qWxPlKmR4s7T
we need drop-down menu for top menu bar
(2) About Fern Vale [ This is single page with some description + imaged and following sub page links should be placed in this page]
2.1 Board of Directors
2.2 Milestones
2.3 Our Logo
2.4 Production & R&D
2.5 Certification and Awards
2.6 Global Presence
2.7 Investors
2.8 Distribution
(3)Ayurveda Pharmaceuticals [ This is one of the 3 main categories ,Category Main Page should provide an introduction to the category]
Following shows the sub categories of the “Ayurvedic Pharmaceuticals” . each subcategory has different products. We need unique design for Main Category Page and Sub category
3.1 Arista
3.2 Asava
3.3 Coorna
3.4 Lepa
3.5 Gritha
3.7 Guggulu
3.8 Kalka
3.9 Kwatha
3.10 Pana
see the wireframe
http://clipmora.net/t/7KrtVm83BQNN
when you click subcategory , we nee a page like this to list products
http://clipmora.net/t/HXwQ5nDe21
(4) Herbal Health Care Products [ This is one of the 3 main categories]
you do not find subcategories, you have only products listed. we need unique design for this category page + products
This page will consists of category description with image and products listed
see the wire frame
(5) Cosmetics & Spa Products
see the wire frame
(6) Essential Oils & Oleoresins
see the wire frame
(7) Media
We need to put video / image gallery / text . and future events
(8) Investors
related information to investors
we need image + text
(9) CSR
(10) Contact US
contact us form / address / telephone number and google map
(11) Log In
Normal login form
(12) Career
Reference Details
http://clipmora.net/t/9PeLcR4TYJ
http://clipmora.net/t/5MgkDRR2Vu
http://clipmora.net/t/bNqVrTHww
Here is a similar site that should give you some idea how we like the new site to look http://www.velkor.com
Industry/Entity Type
Health Care
Requirements
Must have
- We have 4 main categories in our production line
Quality Ayurvedic pharmaceuticals, Herbal health care products, Herbal cosmetics, Essential oils and Oleoresins
You can use 4 boxes below the slider for it ( This very important to have unique different design for each category with some heading, text and images etc)
Nice to have
- You can suggest any good nice features. Try to keep a clean, natural, relaxing theme, with shades of green, white and orange as per their logo. This can be seen from the project brief attachments. www.velkor.com is an example.
Should not have
- Please avoid dark colours (red) and sad colours (grey, black)

```html
<!DOCTYPE html>
<html lang="en">
<head>
<meta charset="utf-8">
<title>Fern Vale – Herbal Health Care</title>
<link href="https://fonts.googleapis.com/css2?family=Arimo:wght@400;700&family=PT+Sans:wght@400;700&display=swap" rel="stylesheet">
<style>
:root{
  --bg-light:#c6ec5a;
  --bg-mid:#8fd321;
  --bg-dark:#5fae12;
  --panel:#ffffff;
  --nav-text:#1f7a2e;
  --body-text:#16703c;
  --heading:#1a1a1a;
  --muted:#6e7a6e;
  --lime:#cde52a;
  --lime-dark:#a9c80f;
  --menu-dark:#2d4a08;
  --rule:#d6e8b8;
}
*{box-sizing:border-box;margin:0;padding:0}
html,body{width:1009px;height:1200px;overflow:hidden}
body{
  position:relative;
  font-family:"Arimo",Arial,sans-serif;
  background:radial-gradient(ellipse at 50% 8%,var(--bg-light) 0,var(--bg-mid) 45%,var(--bg-dark) 100%);
}
.abs{position:absolute}
.brand-tab{left:109px;top:0;width:98px;height:93px;background:linear-gradient(#fff,#eef8dc);border-radius:0 0 8px 8px;box-shadow:0 2px 6px rgba(0,0,0,.15);display:flex;align-items:center;justify-content:center}
.brand-tab span{font-family:"PT Sans",sans-serif;font-weight:700;font-size:17px;color:var(--nav-text)}
.util-links{right:111px;top:15px;font-size:11.5px;color:#fff;letter-spacing:.2px}
.util-links a{color:#fff;text-decoration:none}
.util-links i{font-style:normal;margin:0 8px}
.search-field{left:629px;top:62px;width:234px;height:21px;border-radius:11px;background:linear-gradient(#fff,#e8f4d4);box-shadow:inset 0 1px 3px rgba(0,0,0,.2)}
.search-btn{left:869px;top:55px;width:30px;height:30px;border-radius:50%;background:radial-gradient(circle at 40% 35%,#e9f9c4,#7ec21a);box-shadow:0 1px 3px rgba(0,0,0,.25)}
.main-nav{left:86px;top:122px;width:835px;height:35px;background:linear-gradient(#fff,#eaf7cf);border-radius:6px;display:flex;align-items:center;padding-left:22px;font-family:"PT Sans",sans-serif;font-size:14px;color:var(--nav-text)}
.main-nav a{color:var(--nav-text);text-decoration:none;margin-right:9px;height:35px;line-height:35px}
.main-nav a.active{background:linear-gradient(var(--lime-dark),var(--lime));color:#fff;border-top:3px solid #f29a1f;line-height:32px;padding:0 4px;margin-left:-4px;margin-right:5px}
.content-panel{left:97px;top:157px;width:814px;height:751px;background:var(--panel);box-shadow:0 0 12px rgba(0,0,0,.15)}
.slider{left:118px;top:167px;width:669px;height:231px;background:linear-gradient(160deg,#5d6d3c 0,#cfd3c9 35%,#3b2f22 60%,#e8e6e0 80%,#9a5b3a 100%)}
.slider-dots{left:130px;top:387px;width:99px;height:19px;background:#fff;border-radius:0 0 10px 10px;display:flex;justify-content:space-evenly;align-items:center;box-shadow:0 2px 3px rgba(0,0,0,.15)}
.slider-dots b{width:7px;height:7px;border-radius:50%;background:#8cc21e}
.herb-deco{left:704px;top:316px;width:191px;height:113px;background:radial-gradient(ellipse at 60% 60%,#4e9b22,#a6d466 55%,rgba(255,255,255,0) 75%)}
.dropdown{left:266px;top:161px;width:163px;height:151px;background:linear-gradient(rgba(150,190,20,.92),rgba(205,229,42,.95));box-shadow:0 2px 4px rgba(0,0,0,.2);font-family:"PT Sans",sans-serif;font-size:13.5px;color:var(--menu-dark)}
.dropdown li{list-style:none;height:31px;line-height:31px;padding-left:10px}
.dropdown li.current{background:var(--menu-dark);color:#fff;height:21px;line-height:21px;margin:5px 0}
.category-thumb{top:455px;width:148px;height:110px;border:3px solid #fff;box-shadow:0 0 3px rgba(0,0,0,.3)}
.box{background:#fff;border:1px solid var(--rule)}
.box h3{font-weight:400;font-size:11.5px;color:var(--heading);padding-bottom:5px;border-bottom:1px solid var(--rule)}
.about{left:109px;top:600px;width:444px;height:278px;padding:9px 10px}
.about p{font-size:11.2px;line-height:14px;color:var(--body-text);margin-top:11px;letter-spacing:.1px}
.side-box{border-radius:8px;background:linear-gradient(#fff 40%,#eaf8cf);box-shadow:0 1px 4px rgba(0,0,0,.2);padding:9px 11px}
.subscribe{left:579px;top:599px;width:316px;height:67px}
.email-field{left:589px;top:637px;width:234px;height:27px;border:1px solid var(--rule);background:#fff;font-size:11px;font-style:italic;color:#a8b2a8;padding:6px 7px}
.submit{left:830px;top:642px;font-weight:700;font-size:14px;color:var(--nav-text)}
.testimonials{left:579px;top:690px;width:316px;height:138px}
.avatar{width:42px;height:42px;border:1px solid #cfd8c0;border-radius:6px;background:#fff}
.quote{width:223px;height:41px;background:var(--lime);border:1px solid var(--lime-dark);font-size:11px;font-style:italic;color:#3b6b10;display:flex;align-items:center;justify-content:center}
.blog-bar{left:579px;top:843px;width:316px;height:38px;border-radius:8px;background:linear-gradient(#fff,#e3f5c2);box-shadow:0 1px 4px rgba(0,0,0,.2);font-family:"PT Sans",sans-serif;font-weight:700;font-size:14px;color:#2f8a6a;display:flex;align-items:center;justify-content:center;letter-spacing:.3px}
.product-band{left:97px;top:908px;width:814px;height:183px;background:linear-gradient(#6cbd14,#a3dc37)}
.product{background:linear-gradient(#1e8f3a,#0d5f22);border-radius:4px}
.product.box-pack{background:linear-gradient(#2f9b3c,#7c2d2a)}
.product.jar{background:linear-gradient(#1aa04a 35%,#e8f5e0 36%)}
.band-arrow{width:24px;height:20px}
.product-label{left:162px;top:1072px;width:94px;height:16px;background:#d8ee8a;border-radius:3px;font-size:11px;color:#2c5a10;text-align:center;line-height:16px}
.footer-panel{left:115px;top:1096px;width:780px;height:110px;background:linear-gradient(#fff,#f1fae2);border-radius:8px 8px 0 0}
.footer-head{font-size:11.5px;color:var(--heading);padding-bottom:5px;border-bottom:1px solid var(--rule)}
.small{font-size:10px;color:var(--muted);letter-spacing:.2px}
.mortar-deco{left:0;top:1092px;width:118px;height:108px;background:radial-gradient(ellipse at 40% 60%,#e9e6d8 0,#6fae2a 50%,rgba(0,0,0,0) 75%)}
</style>
</head>
<body>
<div class="abs brand-tab"><span>Fern Vale</span></div>
<nav class="abs util-links"><a href="#">Media</a><i>|</i><a href="#">Investors</a><i>|</i><a href="#">Careers</a><i>|</i><a href="#">CSR</a><i>|</i><a href="#">Contact us</a><i>|</i><a href="#">Log in</a></nav>
<div class="abs search-field"></div>
<div class="abs search-btn">
  <svg width="30" height="30" viewBox="0 0 30 30"><circle cx="13" cy="13" r="5" fill="none" stroke="#fff" stroke-width="2"/><line x1="17" y1="17" x2="22" y2="22" stroke="#fff" stroke-width="3" stroke-linecap="round"/></svg>
</div>

<div class="abs content-panel"></div>
<nav class="abs main-nav">
  <a href="#">Home</a><a href="#">About Fern Vale</a><a href="#" class="active">Ayurveda Pharmaceuticals</a><a href="#">Herbal Health Care Products</a><a href="#">Cosmetics Spa Products</a><a href="#">Essential Oil &amp; Cleansers</a>
</nav>

<div class="abs slider" role="img" aria-label="Dried herbs in white porcelain dishes"></div>
<div class="abs slider-dots"><b></b><b></b><b></b><b></b><b></b></div>
<div class="abs herb-deco" role="img" aria-label="Fresh herbs, bowls and peppercorns"></div>
<ul class="abs dropdown">
  <li>Menu item 01</li><li>Menu item 01</li><li class="current">Menu item 01</li><li>Menu item 01</li><li>Menu item 01</li>
</ul>

<div class="abs category-thumb" style="left:147px;background:linear-gradient(135deg,#f4f2ea,#8fc04a)" role="img" aria-label="Herbal capsules on a green leaf"></div>
<div class="abs category-thumb" style="left:333px;background:linear-gradient(135deg,#8a5a2a,#c99a45,#5a2a18)" role="img" aria-label="Heaps of spices"></div>
<div class="abs category-thumb" style="left:521px;background:linear-gradient(135deg,#c8e67a,#3f8f2a)" role="img" aria-label="Green herb sprigs in a bowl"></div>
<div class="abs category-thumb" style="left:707px;background:linear-gradient(135deg,#b8a060,#f2f2ee,#6e9a3a)" role="img" aria-label="Mortar and pestle with herbs and oil"></div>

<section class="abs box about">
  <h3>About Fern Vale</h3>
  <p>Lorem ipsum dolor sit amet, consectetur adipisicing elit, sed do eiusmod tempor incididunt ut labore et dolore magna aliqua. Ut enim ad minim veniam, quis nostrud exercitation ullamco laboris nisi ut aliquip ex ea commodo consequat. Duis aute irure dolor in reprehenderit in voluptate velit esse cillum dolore eu fugiat nulla pariatur. Excepteur sint occaecat cupidatat non proident, sunt in culpa qui officia deserunt mollit anim id est laborum.</p>
  <p>Lorem ipsum dolor sit amet, consectetur adipisicing elit, sed do eiusmod tempor incididunt ut labore et dolore magna aliqua. Ut enim ad minim veniam, quis nostrud exercitation ullamco laboris nisi ut aliquip ex ea commodo consequat. Duis aute irure dolor in reprehenderit in voluptate velit esse cillum dolore eu fugiat nulla pariatur. Excepteur sint occaecat cupidatat non proident, sunt in culpa qui officia deserunt mollit anim id est laborum.</p>
</section>

<section class="abs side-box subscribe"><h3 style="font-weight:400;font-size:11.5px;padding-bottom:5px;border-bottom:1px solid var(--rule)">Subscribe Via Email</h3></section>
<div class="abs email-field">Your Email</div>
<div class="abs submit">SUBMIT</div>

<section class="abs side-box testimonials"><h3 style="font-weight:400;font-size:11.5px;padding-bottom:5px;border-bottom:1px solid var(--rule)">Testimonials</h3></section>
<div class="abs avatar" style="left:591px;top:726px"></div>
<div class="abs quote" style="left:659px;top:727px">“Sample text”</div>
<div class="abs quote" style="left:591px;top:777px">“Sample text”</div>
<div class="abs avatar" style="left:842px;top:777px"></div>

<div class="abs blog-bar">FERN VALE BLOG</div>

<div class="abs product-band"></div>
<svg class="abs band-arrow" style="left:111px;top:989px" viewBox="0 0 24 20"><path d="M20 3 L6 10 L20 17 Z" fill="#fff"/></svg>
<svg class="abs band-arrow" style="left:876px;top:989px" viewBox="0 0 24 20"><path d="M4 3 L18 10 L4 17 Z" fill="#fff"/></svg>
<div class="abs product" style="left:187px;top:924px;width:42px;height:142px" role="img" aria-label="Herbal hair oil bottle"></div>
<div class="abs product box-pack" style="left:311px;top:999px;width:47px;height:63px" role="img" aria-label="Herbal powder pack"></div>
<div class="abs product jar" style="left:433px;top:1006px;width:38px;height:58px" role="img" aria-label="Herbal balm jar"></div>
<div class="abs product" style="left:543px;top:924px;width:42px;height:142px" role="img" aria-label="Herbal hair oil bottle"></div>
<div class="abs product box-pack" style="left:667px;top:999px;width:47px;height:63px" role="img" aria-label="Herbal powder pack"></div>
<div class="abs product jar" style="left:789px;top:1006px;width:38px;height:58px" role="img" aria-label="Herbal balm jar"></div>
<div class="abs product-label">Product name</div>

<div class="abs footer-panel"></div>
<div class="abs mortar-deco" role="img" aria-label="Mortar with herbs and leaves"></div>
<div class="abs" style="left:138px;top:1124px;width:52px;height:52px;border-radius:50%;background:#d9efb0"></div>
<div class="abs" style="left:209px;top:1101px;width:266px">
  <div class="footer-head">Chirpline Feeds</div>
  <div class="small" style="margin-top:13px;padding-bottom:8px;border-bottom:1px solid var(--rule)">Chirpline Feed 01</div>
  <div class="small" style="margin-top:12px">Chirpline Feed 02</div>
</div>
<svg class="abs" style="left:519px;top:1129px" width="38" height="38" viewBox="0 0 38 38"><circle cx="19" cy="19" r="18" fill="#eef7e2" stroke="#cfe3b5"/><path d="M12 11c2-2 4-1 5 1l1 3c0 1-1 2-2 2 1 3 3 5 6 6 0-1 1-2 2-2l3 1c2 1 3 3 1 5-3 3-8 1-12-3s-6-9-4-13z" fill="#4aa11e"/></svg>
<div class="abs" style="left:579px;top:1101px;width:308px">
  <div class="footer-head">Contact Details</div>
  <div class="small" style="margin-top:7px;display:grid;grid-template-columns:76px 1fr;row-gap:1px;line-height:11.5px">
    <span>Address:</span><span>48, Palm Grove Lane,<br>Harbourview 04<br>Sri Lanka</span>
    <span>E-mail:</span><span>hello@fernvaleherbals.com</span>
    <span>Telephone:</span><span>(+94 11) 5550148/ 5550172</span>
  </div>
</div>
</body>
</html>
```